Fresh mango cartoon design with atractive apparance

I need cartoon desgin for fresh alfonso mango imported from india i have my own logo but i need the cartoon desgin with a slogen name for the mango for example (tilvor) or( ronex )or any good name easy to remember with rethem i need it fancy notable click to any one sees the cartoon
The cartoon is rectangle the measurement are 36cm long by 26cm width by 8cm hight and the cartoon Weigh 260 grams empty
Ineed my company name and logo the cartoon color should rime with logo colors or something good with it

Not yet satisfied with what I got maybe because of short periods of time there for i want to get extra time so the designers have time to be more creative Thanks for all designers who submitted their design

Local fruit market and hapermarket in kuwait

Sans Serif

• Attracted design easy to remember and creative also must have the weight of the mango proximitly 3 kg . Grade Aproduct ,
• fance realaity pic of mango if possible. My company logo and insagram add.
• Not really

```html
<!DOCTYPE html>
<html lang="en">
<head>
<meta charset="utf-8">
<title>Ronex Mango Carton Panel</title>
<link rel="stylesheet" href="https://fonts.googleapis.com/css2?family=Jost:wght@600;700&family=Cairo:wght@800&display=swap">
<style>
  :root {
    --frame-green: #33512a;
    --band-green: #34ae2b;
    --panel-white: #ffffff;
    --brand-brown: #613a1a;
    --mango-light: #fbb03b;
    --mango-mid: #f7a12d;
    --mango-deep: #f27a22;
    --leaf-green: #3db54a;
    --company-green: #5a9a3c;
  }
  * { margin: 0; padding: 0; box-sizing: border-box; }
  html, body {
    width: 1139px;
    height: 1200px;
    overflow: hidden;
    background: var(--frame-green);
  }
  .carton-panel {
    position: relative;
    width: 1139px;
    height: 1200px;
    background: var(--frame-green);
  }
  .brand-panel {
    position: absolute;
    left: 68px;
    top: 42px;
    width: 992px;
    height: 883px;
    background: var(--panel-white);
  }
  .mango-artwork {
    position: absolute;
    left: 335px;
    top: 50px;
    width: 320px;
    height: 330px;
    border-radius: 58% 42% 50% 50% / 40% 45% 55% 60%;
    transform: rotate(28deg);
    background: radial-gradient(circle at 40% 40%, var(--mango-light), var(--mango-mid) 60%, var(--mango-deep));
  }
  .product-name {
    position: absolute;
    left: 0;
    width: 100%;
    top: 360px;
    text-align: center;
    font-family: "Jost", sans-serif;
    font-weight: 700;
    font-size: 300px;
    line-height: 1;
    letter-spacing: -4px;
    color: var(--brand-brown);
  }
  .slogan-band {
    position: absolute;
    left: 0;
    bottom: 0;
    width: 100%;
    height: 109px;
    background: var(--band-green);
    display: flex;
    align-items: center;
    padding-left: 85px;
  }
  .slogan-text {
    font-family: "Jost", sans-serif;
    font-weight: 600;
    font-size: 63px;
    letter-spacing: 2px;
    color: var(--panel-white);
  }
  .company-panel {
    position: absolute;
    left: 68px;
    top: 957px;
    width: 992px;
    height: 188px;
    background: var(--panel-white);
    display: flex;
    align-items: center;
    justify-content: center;
    gap: 16px;
  }
  .company-dot {
    width: 44px;
    height: 44px;
    border-radius: 50%;
    background: var(--company-green);
  }
  .company-name {
    font-family: "Cairo", sans-serif;
    font-weight: 800;
    font-size: 54px;
    color: var(--brand-brown);
  }
</style>
</head>
<body>
  <main class="carton-panel">
    <section class="brand-panel">
      <div class="mango-artwork" role="img" aria-label="Illustration of a ripe orange mango with a green leaf"></div>
      <h1 class="product-name">ronex</h1>
      <div class="slogan-band">
        <p class="slogan-text">FRESH TASTY MANGO</p>
      </div>
    </section>
    <section class="company-panel">
      <span class="company-dot"></span>
      <p class="company-name" lang="ar" dir="rtl">متجر نخيلي</p>
    </section>
  </main>
</body>
</html>
```